Professional Website for Leading Global Private Equity Real Estate Company

The company is a leading global Private Equity Real Estate (PERE). We need a homepage design, an inner page design, and color/font tweaks to the logo (color should be more soothing than current blue used in the logo). The logo website should project the company as global, professional, experienced, trustworthy, accessible, YOUNG, DYNAMIC, hi-tech. PLEASE SEE the attached Design Brief Word Doc for details.

Target Market(s)

institional investors and wealthy private individuals

Industry/Entity Type

Finance

Number of Pages Required

2 page

Font styles to use
Sans Serif
Other font styles liked:
• either like in https://www.ferndalequay.com/ or like in presentations (Montserrat Black & Montserrat Light, Century Gothic, Blair ITC, Almoni Neue DL 4.0 AAA Medium, Almoni DL AAA)

Requirements
Must have
• new color palette that is NOT based on current logo. they want a more soothing color palette than the blue in that logo. the new color palette should project: global, professional, experienced, trustworthy, accessible, YOUNG, DYNAMIC, hi-tech.
Nice to have
• the likes these sites: https://www.ferndalequay.com/ and https://www.tvr.law/

```html
<!DOCTYPE html>
<html lang="en">
<head>
<meta charset="utf-8">
<title>Corvane Real Estate</title>
<link rel="stylesheet" href="https://fonts.googleapis.com/css2?family=Montserrat:wght@300;400;500;600;700;900&display=swap">
<style>
:root{
  --gold:#c9a043;
  --gold-dark:#b48a30;
  --ink:#3a3a3a;
  --dark:#1d1d1d;
  --dark-2:#262626;
  --cream:#faf3e6;
  --text:#555;
  --white:#fff;
}
*{box-sizing:border-box;margin:0;padding:0}
html,body{width:1200px;height:4448px;overflow:hidden}
body{font-family:"Montserrat",sans-serif;color:var(--text);background:var(--white);position:relative}
section,header,footer{position:relative;width:1200px;overflow:hidden}
.btn{display:inline-block;background:var(--gold);color:var(--white);font-weight:600;font-size:15px;border-radius:22px;text-align:center}
.heading{font-weight:900;color:var(--ink);letter-spacing:.5px}

/* top bar */
.topbar{height:79px;background:var(--dark);color:var(--white);font-size:14px}
.topbar .mail{position:absolute;left:162px;top:28px;display:flex;align-items:center;gap:8px}
.dot-icon{width:26px;height:26px;border-radius:50%;background:var(--gold);display:flex;align-items:center;justify-content:center}
.brand{position:absolute;left:505px;top:16px;text-align:center}
.brand .name{font-weight:700;font-size:26px;letter-spacing:3px;display:flex;align-items:center;gap:8px}
.brand .name i{width:30px;height:30px;border-radius:50%;background:var(--gold);display:inline-block}
.brand .sub{font-size:10px;color:var(--gold);letter-spacing:2px;margin-left:36px}
.topbar .login{position:absolute;right:162px;top:26px;display:flex;align-items:center;gap:8px}

/* nav */
.nav{height:59px;background:var(--gold)}
.nav ul{list-style:none;display:flex;justify-content:space-between;padding:0 145px 0 160px;line-height:59px;color:var(--white);font-size:13px;font-weight:500}

/* hero */
.hero{height:506px;background:linear-gradient(180deg,#4a5a70 0%,#2d3a4c 55%,#1a2230 100%)}
.hero .photo{position:absolute;inset:0}
.hero h1{position:absolute;top:160px;width:100%;text-align:center;color:var(--white);font-size:44px;font-weight:900;line-height:60px}
.hero .btn{position:absolute;left:538px;top:305px;width:124px;height:40px;line-height:40px;font-size:14px;padding-left:26px}
.hero .btn i{position:absolute;left:8px;top:9px;width:22px;height:22px;border-radius:50%;background:var(--white)}

/* about */
.about{height:725px;text-align:center}
.about h2{position:absolute;top:66px;width:100%;font-size:40px}
.about p{position:absolute;left:230px;width:740px;font-size:13.5px;line-height:26px}
.about .p1{top:130px}.about .p2{top:196px}
.about .btn{position:absolute;left:530px;top:296px;width:140px;height:42px;line-height:42px}
.stats{position:absolute;left:161px;top:397px;width:877px;height:216px;border:1px solid #e5d1a4;border-radius:8px;background:linear-gradient(100deg,#fbf6ec,#fff 50%,#fbf3e4);display:flex}
.stat{flex:1;position:relative;text-align:center;padding-top:38px}
.stat+.stat:before{content:"";position:absolute;left:0;top:26px;height:160px;border-left:1px solid #e2d3b4}
.ring{width:90px;height:90px;border:2px solid var(--gold);border-radius:50%;margin:0 auto;line-height:86px;font-weight:900;font-size:26px;color:var(--ink)}
.stat b{display:block;margin-top:12px;font-size:15px;color:var(--ink);font-weight:600}
.stat span{font-size:13px}

/* platforms */
.platforms{height:675px;background:linear-gradient(180deg,#141414,#2a2a2a)}
.platforms h2{position:absolute;top:100px;width:100%;text-align:center;color:var(--white);font-size:42px;font-weight:900}
.cards{position:absolute;top:190px;left:0;display:flex}
.card{width:240px;height:373px;background:var(--dark-2);text-align:center;color:#d8d8d8;padding-top:38px}
.card:nth-child(even){background:#111}
.card.active{background:linear-gradient(180deg,#7c6f62,#3d3a3a 60%,#5a4a1e);border:1px solid var(--gold)}
.card .mark{width:50px;height:50px;border-radius:50%;background:#3ab0e0;margin:0 auto}
.card .nm{margin-top:12px;font-size:22px;font-weight:700;letter-spacing:3px;color:#ddd}
.card .cat{font-size:15px;letter-spacing:1px;margin-top:2px}
.card p{font-size:12.5px;line-height:24.5px;padding:0 28px;margin-top:6px}
.card .more{display:inline-block;margin-top:28px;width:120px;height:36px;line-height:34px;border:1px solid var(--gold);border-radius:18px;color:var(--white);font-size:14px;font-weight:500}
.card.active .more{background:var(--gold)}

/* split sections */
.split{height:525px}
.split h2{font-size:40px}
.split .copy{position:absolute;top:110px;width:420px}
.split p{font-size:13.5px;line-height:27px;margin-top:14px;color:#444}
.split p strong{font-weight:700}
.split .btn{margin-top:24px;width:224px;height:46px;line-height:46px}
.edge .copy{left:162px}
.edge .photo{position:absolute;left:660px;top:0;width:540px;height:525px;background:linear-gradient(135deg,#e8eaee,#8a96a8 55%,#4a3a30)}
.resp{height:525px}
.resp .copy{left:617px;top:112px}
.resp .photo{position:absolute;left:0;top:0;width:540px;height:525px;background:linear-gradient(135deg,#3a3a3a,#5a5a5a 50%,#b08850)}

/* newsletter */
.news{height:391px;background:linear-gradient(90deg,#b8944a,#d4ad58 50%,#c9a043);text-align:center;color:var(--white)}
.news h2{position:absolute;top:100px;width:100%;font-size:40px;font-weight:900}
.news p{position:absolute;top:168px;left:200px;width:800px;font-size:15px;line-height:24px}
.news form{position:absolute;left:296px;top:236px;width:608px;height:42px;background:var(--white);border-radius:21px}
.news form span{position:absolute;left:46px;top:12px;color:#888;font-size:13px}
.news form i{position:absolute;left:24px;top:15px;width:12px;height:9px;background:var(--gold)}
.news form b{position:absolute;right:0;top:0;width:150px;height:42px;line-height:42px;background:#111;color:var(--white);border-radius:21px;font-size:15px}

/* contact */
.contact{height:607px;background:var(--cream);text-align:center}
.contact h2{position:absolute;top:98px;width:100%;font-size:40px}
.contact>p{position:absolute;top:162px;left:230px;width:740px;font-size:13.5px;line-height:23px}
.field{position:absolute;height:36px;border:1px solid #e0d6c4;background:var(--white);text-align:left;font-size:11px;color:#888;padding:11px 0 0 40px}
.field i{position:absolute;left:12px;top:10px;width:16px;height:16px;border:1.5px solid var(--gold);border-radius:50%}
.contact .btn{position:absolute;left:514px;top:450px;width:172px;height:42px;line-height:42px}

/* footer */
.footer{height:308px;background:var(--white)}
.footer h4{color:var(--gold);font-size:16px;font-weight:700;margin-bottom:18px}
.col{position:absolute;top:70px;font-size:13px;color:#333}
.col li{list-style:none;line-height:27px}
.cd{display:flex;gap:14px;margin-bottom:16px;line-height:22px}
.cd i{flex:none;width:28px;height:28px;border-radius:50%;background:var(--gold);margin-top:6px}
.cd b{font-weight:700}
.fbrand .name{font-weight:700;font-size:24px;letter-spacing:3px;color:#333;display:flex;align-items:center;gap:8px}
.fbrand .name i{width:30px;height:30px;border-radius:50%;background:var(--gold)}
.fbrand .sub{font-size:10px;color:var(--gold);letter-spacing:2px;margin-left:48px}
.fbrand p{margin-top:12px;line-height:27px}
.bottombar{height:48px;background:#4a4a4a;color:#ddd;font-size:11.5px}
.bottombar span{position:absolute;left:162px;top:17px}
.social{position:absolute;right:162px;top:11px;display:flex;gap:8px}
.social i{width:26px;height:26px;border-radius:50%;background:var(--gold)}
</style>
</head>
<body>

<header class="topbar">
  <div class="mail"><span class="dot-icon"><svg width="12" height="9" viewBox="0 0 12 9"><rect x=".5" y=".5" width="11" height="8" fill="none" stroke="#fff"/><path d="M.5 .5 6 5l5.5-4.5" fill="none" stroke="#fff"/></svg></span>info@corvane.com</div>
  <div class="brand"><div class="name"><i></i>CORVANE</div><div class="sub">REAL ESTATE</div></div>
  <div class="login"><span class="dot-icon"><svg width="12" height="13" viewBox="0 0 12 13"><circle cx="6" cy="4" r="3" fill="none" stroke="#fff"/><path d="M1 12.5c0-3 2-4.5 5-4.5s5 1.5 5 4.5" fill="none" stroke="#fff"/></svg></span>Login</div>
</header>

<nav class="nav"><ul><li>Home</li><li>About Us</li><li>Our Businesses</li><li>Investors</li><li>News</li><li>Contact Us</li></ul></nav>

<section class="hero">
  <div class="photo" role="img" aria-label="Upward view of glass office towers against a cloudy sky"></div>
  <h1>We are leading global Private<br>Equity Real Estate Firm</h1>
  <span class="btn"><i></i>About Us</span>
</section>

<section class="about">
  <h2 class="heading">About Us</h2>
  <p class="p1">Corvane Consumer Products, of the Arlo Group, which was founded in 1951, is the longest-standing and leading company in Israel in the area of home electrical appliances and air conditioning.</p>
  <p class="p2">The Company is engaged in the production, import, export, sales, distribution, marketing and provision of services for a broad variety of consumer electrical appliances. The Company has an annual sales turnover of NIS 2.49 billion and it employs around 1,600 employees.</p>
  <span class="btn">Read More</span>
  <div class="stats">
    <div class="stat"><div class="ring">4.6</div><b>NIS Bilion</b><span>Annual Revenues</span></div>
    <div class="stat"><div class="ring">265</div><b>NIS Million</b><span>Annual Operating Income</span></div>
    <div class="stat"><div class="ring">164</div><b>NIS Million</b><span>Annual net profit</span></div>
    <div class="stat"><div class="ring">1.2</div><b>NIS Billion</b><span>equity</span></div>
  </div>
</section>

<section class="platforms">
  <h2>Our Investment Platforms</h2>
  <div class="cards">
    <div class="card"><div class="mark"></div><div class="nm">CORVANE</div><div class="cat">MULTIFAMILY</div><p>Lorem ipsum dolor sit amet, consectetuer adipiscing elit, sed diam nonummy nibh euismod tincidunt ut</p><span class="more">Read More</span></div>
    <div class="card"><div class="mark"></div><div class="nm">CORVANE</div><div class="cat">DEBT</div><p>Lorem ipsum dolor sit amet, consectetuer adipiscing elit, sed diam nonummy nibh euismod tincidunt ut</p><span class="more">Read More</span></div>
    <div class="card active" role="img" aria-label="Family at home in warm light behind the platform card"><div class="mark"></div><div class="nm">CORVANE</div><div class="cat">SINGLE FAMILY</div><p>Lorem ipsum dolor sit amet, consectetuer adipiscing elit, sed diam nonummy nibh euismod tincidunt ut</p><span class="more">Read More</span></div>
    <div class="card"><div class="mark"></div><div class="nm">CORVANE</div><div class="cat">HOSPITALITY</div><p>Lorem ipsum dolor sit amet, consectetuer adipiscing elit, sed diam nonummy nibh euismod tincidunt ut</p><span class="more">Read More</span></div>
    <div class="card"><div class="mark"></div><div class="nm">CORVANE</div><div class="cat">UK</div><p>Lorem ipsum dolor sit amet, consectetuer adipiscing elit, sed diam nonummy nibh euismod tincidunt ut</p><span class="more">Read More</span></div>
  </div>
</section>

<section class="split edge">
  <div class="copy">
    <h2 class="heading">Our Edge</h2>
    <p>Lorem ipsum dolor sit amet, consectetuer adipiscing elit, sed diam nonummy nibh euismod tincidunt ut laoreet dolore magna aliquam erat volutpat.</p>
    <p>Ut wisi enim ad minim veniam, quis nostrud exerci tation ullamcorper <strong>suscipit lobortis</strong> nisl ut aliquip ex ea commodo consequat. Duis autem vel eum iriure dolor in hendrerit in vulputate velit esse molestie consequat</p>
    <span class="btn">Investor Information</span>
  </div>
  <div class="photo" role="img" aria-label="Business presentation in front of a large trading chart screen"></div>
</section>

<section class="news" role="region" aria-label="Newsletter signup over a softly tinted office photo">
  <h2>Stay Updated</h2>
  <p>Lorem ipsum dolor sit amet, consectetuer adipiscing elit, sed diam nonummy nibh euismod tincidunt ut laoreet dolore magna aliquam erat volutpat.</p>
  <form><i></i><span>Email Address</span><b>Subcribe</b></form>
</section>

<section class="split resp">
  <div class="photo" role="img" aria-label="Hand stopping a row of falling wooden blocks"></div>
  <div class="copy">
    <h2 class="heading">Our Responsibility</h2>
    <p>Lorem ipsum dolor sit amet, consectetuer adipiscing elit, sed diam nonummy nibh euismod tincidunt ut laoreet dolore magna aliquam erat volutpat.</p>
    <p>Ut wisi enim ad minim veniam, quis nostrud exerci tation ullamcorper <strong>suscipit lobortis</strong> nisl ut aliquip ex ea commodo consequat. Duis autem vel eum iriure dolor in hendrerit in vulputate velit esse molestie consequat</p>
    <span class="btn">Investor Information</span>
  </div>
</section>

<section class="contact">
  <h2 class="heading">Contact Form</h2>
  <p>If you have any questions about Corvane, and are interested in speaking with us about adding services for your home or business, please get in touch with us using the information</p>
  <div class="field" style="left:300px;top:232px;width:292px"><i></i>Name</div>
  <div class="field" style="left:608px;top:232px;width:292px"><i style="border-radius:2px"></i>Email</div>
  <div class="field" style="left:300px;top:284px;width:292px"><i></i>Phone</div>
  <div class="field" style="left:608px;top:284px;width:292px"><i style="border-radius:2px"></i>Company</div>
  <div class="field" style="left:300px;top:336px;width:600px;height:88px"><i></i>Message</div>
  <span class="btn">Get In Touch</span>
</section>

<footer class="footer">
  <div class="col" style="left:162px"><h4>Quick Links</h4><ul><li>Home</li><li>About Us</li><li>Our Businesses</li><li>Investors</li><li>News</li><li>Contact Us</li></ul></div>
  <div class="col" style="left:344px"><h4>Our Businesses</h4><ul><li>Corvane Multifamily</li><li>Corvane Debt</li><li>Corvane Single Family</li><li>Corvane Hospitality</li><li>Corvane UK</li></ul></div>
  <div class="col" style="left:561px;width:200px"><h4>Contact Detail</h4>
    <div class="cd"><i></i><span>Nonummy euismod tincidunt - 987 658</span></div>
    <div class="cd"><i></i><span><b>Phone</b><br>+987 654 0192</span></div>
    <div class="cd"><i></i><span><b>Email</b><br>info@corvane.com</span></div>
  </div>
  <div class="col fbrand" style="left:815px;top:60px;width:230px">
    <div class="name"><i></i>CORVANE</div><div class="sub">REAL ESTATE</div>
    <p>Lorem ipsum dolor sit amet, consectetuer adipiscing elit, sed diam nonummy nibh euismod tincidunt ut laoreet dolore magna aliquam erat volutpat.</p>
  </div>
</footer>

<div class="bottombar" style="position:relative">
  <span>Copyright © 2022 Corvane. All Rights Reserved.</span>
  <div class="social"><i></i><i></i><i></i></div>
</div>

</body>
</html>
```